Anzeigengestaltung für Fliesenlegermeister
Zielgruppe
Ich bin ein Fliesenlegermeister und möchte mich selbstständig machen, ich saniere Bäder, Böden mit Fliesen, Fliesenspiegel und ich möchte eine Anzeige in den regionalen Zeitungen machen. Ich spreche alle Altersklassen mit Bädern für Sanierungen, Bodenfliesen und Neubauten an. Reparatur und Silikonarbeiten sowie Trockenbauarbeiten am eigenen Heim .
Aufgabenstellung
Ich möchte gern meine Kontaktdaten und die Farben vom Logo wieder finden,
als Beispiel habe ich meine aktuelle Visitenkarte beigefügt Dort finden sich die Kontaktdaten. Meine Arbeiten sind insbesondere :
Fliesenverlegung
Badsanierung
barrierefreie Bäder
Reparaturarbeiten
Silikonarbeiten
Trockenbau
Ob nun genau alle 6 Punkte in der Anzeige angezeigt werden soll bin ich mir nicht sicher oder ob nur 4 Beschreibungen reichen, damit es nicht zu viel wird.

```html
<!DOCTYPE html>
<html lang="de">
<head>
<meta charset="utf-8">
<title>Anzeige Fliesenlegermeister Jonas Wernick</title>
<link href="https://fonts.googleapis.com/css2?family=Michroma&family=Open+Sans:ital,wght@0,400;0,600;1,400;1,600&display=swap" rel="stylesheet">
<style>
  :root {
    --brand-blue: #0d4a9a;
    --brand-grey: #4a4a4a;
    --panel-grey: rgba(62, 62, 62, 0.78);
    --cta-red: #d42a1f;
    --paper: #f4f4f2;
    --white: #ffffff;
    --photo-light: #d9d4cc;
    --photo-dark: #8a8580;
  }
  * { box-sizing: border-box; margin: 0; padding: 0; }
  html, body { width: 1200px; height: 788px; overflow: hidden; background: var(--paper); }
  .ad {
    position: relative;
    width: 1200px;
    height: 788px;
    overflow: hidden;
    background: var(--paper);
    font-family: "Open Sans", sans-serif;
  }
  .ad__photo {
    position: absolute;
    left: 0; top: 0;
    width: 1200px; height: 690px;
    background: linear-gradient(115deg, var(--photo-light) 0%, #c9c2b8 35%, #a9a39c 60%, var(--photo-dark) 100%);
  }
  .ad__footer-band {
    position: absolute;
    left: 0; top: 640px;
    width: 1200px; height: 148px;
    background: var(--white);
  }
  .brand {
    position: absolute;
    left: 560px; top: 40px;
    width: 610px; height: 150px;
    background: var(--white);
    display: flex;
    align-items: center;
    padding-left: 40px;
    gap: 28px;
  }
  .brand__mark {
    width: 54px; height: 54px;
    background: var(--brand-blue);
    flex: none;
  }
  .brand__text { border-left: 2px solid var(--brand-grey); padding-left: 22px; }
  .brand__name {
    font-family: "Michroma", sans-serif;
    font-size: 44px;
    line-height: 1.1;
    color: var(--brand-blue);
    letter-spacing: 1px;
  }
  .brand__title {
    font-family: "Michroma", sans-serif;
    font-size: 19px;
    color: var(--brand-grey);
    letter-spacing: 2px;
    margin-top: 6px;
  }
  .services {
    position: absolute;
    left: 540px; top: 190px;
    width: 630px; height: 430px;
    background: var(--panel-grey);
    padding: 34px 0 0 40px;
    list-style: none;
  }
  .services__item {
    font-family: "Michroma", sans-serif;
    font-size: 27px;
    color: var(--white);
    letter-spacing: 2px;
    line-height: 62px;
    display: flex;
    align-items: center;
    gap: 22px;
  }
  .services__item::before {
    content: "";
    width: 16px; height: 16px;
    background: var(--white);
    transform: rotate(45deg);
    flex: none;
  }
  .project-type {
    position: absolute;
    left: 0; top: 470px;
    width: 390px; height: 175px;
    background: var(--brand-blue);
    color: var(--white);
    font-size: 42px;
    font-style: italic;
    line-height: 1.15;
    letter-spacing: 2px;
    padding: 28px 0 0 36px;
  }
  .cta {
    position: absolute;
    left: 280px; top: 560px;
    width: 280px; height: 150px;
    background: var(--cta-red);
    color: var(--white);
    font-size: 34px;
    font-style: italic;
    line-height: 1.05;
    letter-spacing: 1px;
    padding: 24px 0 0 30px;
  }
  .contact {
    position: absolute;
    left: 600px; top: 660px;
    color: var(--brand-blue);
    font-size: 21px;
    line-height: 1.35;
  }
  .corner {
    position: absolute;
    right: 0; bottom: 0;
  }
</style>
</head>
<body>
<div class="ad">
  <div class="ad__photo" role="img" aria-label="Foto: fröhliches Kind im weißen Bademantel in einem hellen, modernen Badezimmer"></div>
  <div class="ad__footer-band"></div>

  <div class="brand">
    <div class="brand__mark"></div>
    <div class="brand__text">
      <div class="brand__name">JONAS WERNICK</div>
      <div class="brand__title">FLIESENLEGERMEISTER</div>
    </div>
  </div>

  <ul class="services">
    <li class="services__item">Fliesenverlegung</li>
    <li class="services__item">Badsanierung</li>
    <li class="services__item">Barrierefreie Bäder</li>
    <li class="services__item">Reparaturarbeiten</li>
    <li class="services__item">Silikonarbeiten</li>
    <li class="services__item">Trockenbau</li>
  </ul>

  <div class="project-type">SANIERUNG/<br>NEUBAU</div>

  <div class="cta">JETZT<br>ANGEBOT<br>EINHOLEN</div>

  <div class="contact">
    05301/4418270 Mobil 01715523904<br>
    info@fliesen-wernick.de<br>
    Lindenweg 7, 38100 Musterstadt
  </div>

  <svg class="corner" width="330" height="260" viewBox="0 0 330 260" aria-hidden="true">
    <polygon points="330,0 330,260 160,160" fill="#4a4848"/>
    <polygon points="0,260 180,140 250,260" fill="#0d4a9a"/>
  </svg>
</div>
</body>
</html>
```